Group training gym/bootcamp needs a web design

We need a website for our gym that is based in Sydney. We have indoor functional training classes and outdoor bootcamp classes. We would like the web site to have a video (to be created) and photo gallery. I would like the site made on word press and i would like to be able to make minor changes such as changing images and text without having to use a designer.

The website should have the following pages: home page; the gym; the bootcamp; photo gallery; about us; contact.

I have uploaded our logo and i would like to keep to these colour (blue,yellow,silver) and black is also allowed

Target Market(s)

18-50 male and female

Industry/Entity Type

Gym

Coding

Coded - Design and coding required

Number of Pages Required

5+ page

Font styles to use
Sans Serif

Colors
0692cd
fbed22
1b1b1b
e8e8e8

Requirements
Must have
• The website should have the following pages: home page; the gym; the bootcamp; photo gallery; about us; contact.
• I have uploaded our logo and i would like to keep to these colour (blue,yellow,silver) and black is also allowed
• Video upload and photo upload

```html
<!DOCTYPE html>
<html lang="en">
<head>
<meta charset="utf-8">
<title>Coreline Fitness Studio</title>
<link rel="stylesheet" href="https://fonts.googleapis.com/css2?family=Raleway:wght@400;600;700;800&family=Open+Sans:wght@400;600&display=swap">
<style>
:root{
  --blue:#0692cd;
  --blue-deep:#0a6fae;
  --yellow:#fbed22;
  --ink:#1b1b1b;
  --silver:#e8e8e8;
  --grey-text:#777;
  --white:#fff;
}
*{margin:0;padding:0;box-sizing:border-box}
html,body{width:1200px;height:2816px;overflow:hidden;background:var(--white)}
body{position:relative;font-family:"Open Sans",Arial,sans-serif;color:var(--ink)}
.abs{position:absolute}
h1,h2,h3,.nav a,.brand,.btn{font-family:"Raleway",Arial,sans-serif}

/* header */
.site-header{left:0;top:0;width:1200px;height:112px;background:var(--white)}
.brand{left:150px;top:28px;display:flex;align-items:center;gap:12px;font-weight:800;font-size:22px;color:var(--blue);text-transform:uppercase;letter-spacing:.5px;line-height:1.05}
.brand-dot{width:46px;height:46px;border-radius:50%;background:var(--yellow)}
.nav{right:150px;top:48px;display:flex;gap:26px}
.nav a{font-size:13px;font-weight:600;color:#444;text-decoration:none;letter-spacing:.3px}
.nav a.active{color:var(--blue)}

/* hero */
.hero{left:0;top:112px;width:1200px;height:570px;background:linear-gradient(180deg,#c9dbe6 0%,#9bb3c2 45%,#6f6a5e 75%,#4a463e 100%)}
.hero-box{left:150px;top:290px;width:410px;height:210px;background:rgba(27,27,27,.55);padding:26px 24px}
.hero-kicker{font-family:"Raleway",sans-serif;font-weight:700;color:var(--yellow);font-size:20px;text-transform:uppercase}
.hero-title{font-weight:800;color:var(--white);font-size:33px;line-height:1.1;text-transform:uppercase;margin-top:6px}
.btn-yellow{display:inline-block;margin-top:16px;background:var(--yellow);color:var(--ink);font-weight:700;font-size:12px;padding:10px 18px;text-transform:uppercase}
.dots{display:flex;gap:8px}
.dots span{width:10px;height:10px;border-radius:50%;background:rgba(255,255,255,.6)}
.dots span.on{background:var(--white)}
.hero .dots{position:absolute;left:570px;top:510px}

/* welcome */
.welcome-mark{left:578px;top:718px;width:44px;height:44px;border-radius:50%;background:var(--blue);border:4px solid var(--yellow)}
.section-title{width:1200px;left:0;text-align:center;font-weight:800;text-transform:uppercase;color:var(--ink)}
.welcome-title{top:790px;font-size:29px}
.welcome-text{left:300px;top:845px;width:600px;text-align:center;font-size:13px;line-height:1.75;color:var(--grey-text)}

/* class cards */
.card{top:1005px;width:448px;height:300px;text-align:center;padding-top:38px}
.card-outdoor{left:142px;background:var(--blue);color:var(--white)}
.card-indoor{left:610px;background:var(--yellow);color:var(--ink)}
.card h3{font-size:23px;font-weight:800;text-transform:uppercase;line-height:1.15;margin-top:14px}
.card p{width:300px;margin:12px auto 0;font-size:12px;line-height:1.6}
.card .arrow{position:absolute;right:20px;bottom:18px}

/* gallery */
.gallery{left:0;top:1330px;width:1200px;height:510px;background:linear-gradient(115deg,var(--blue-deep) 0%,var(--blue) 35%,#2fa6de 55%,var(--blue) 75%,var(--blue-deep) 100%);clip-path:polygon(0 40px,1200px 0,1200px 470px,0 510px)}
.gallery-title{top:1410px;color:var(--white);font-size:27px}
.gallery-photo{top:1490px;width:225px;height:220px}
.gallery .dots{position:absolute}
.gallery-dots{left:545px;top:1745px}
.gallery-dots span{width:22px;height:4px;border-radius:2px}

/* videos */
.videos-title{top:1878px;font-size:21px}
.video-thumb{top:1935px;width:290px;height:190px;border:5px solid var(--white);box-shadow:0 4px 12px rgba(0,0,0,.3)}
.play{position:absolute;left:50%;top:50%;transform:translate(-50%,-50%)}

/* join */
.join{left:0;top:2190px;width:1200px;height:450px;background:linear-gradient(180deg,#3a3f2c 0%,#2a2a24 55%,#1b1b1b 100%);clip-path:polygon(0 0,1200px 60px,1200px 450px,0 450px)}
.join-title{top:2350px;color:var(--white);font-size:33px}
.join-text{left:360px;top:2400px;width:480px;text-align:center;color:var(--white);font-size:13px;line-height:1.6}
.btn-outline{left:540px;top:2468px;width:120px;height:38px;border:2px solid var(--yellow);color:var(--yellow);font-size:12px;font-weight:700;text-transform:uppercase;display:flex;align-items:center;justify-content:center}

/* footer */
.footer{left:0;top:2640px;width:1200px;height:176px;background:var(--white)}
.footer-nav{left:146px;top:2700px;display:flex;gap:20px}
.footer-nav a{font-size:12px;font-weight:700;color:var(--ink);text-decoration:none}
.copyright{left:146px;top:2738px;font-size:12px;color:var(--grey-text)}
.social{left:852px;top:2700px;display:flex;gap:8px}
.social span{width:28px;height:28px;border-radius:50%;border:1.5px solid var(--ink)}
</style>
</head>
<body>

<header class="site-header abs">
  <div class="brand abs"><span class="brand-dot"></span><span>Coreline<br>Fitness Studio</span></div>
  <nav class="nav abs">
    <a class="active" href="#">HOME</a><a href="#">THE GYM</a><a href="#">THE BOOTCAMP</a><a href="#">PHOTO GALLERY</a><a href="#">ABOUT US</a><a href="#">CONTACT US</a>
  </nav>
</header>

<section class="hero abs" role="img" aria-label="People training on an outdoor fitness rig by the waterfront">
  <div class="dots"><span class="on"></span><span></span><span></span><span></span></div>
</section>
<div class="hero-box abs">
  <div class="hero-kicker">Want a fit body</div>
  <h1 class="hero-title">Join Coreline<br>Fitness Studio</h1>
  <span class="btn btn-yellow">Join now</span>
</div>

<div class="welcome-mark abs"></div>
<h2 class="section-title welcome-title abs">Welcome to our website</h2>
<p class="welcome-text abs">Our coaches run small group sessions built around strength, conditioning and mobility. Every class is scaled to your level, so beginners and athletes train side by side. Come along, meet the team and find the session that fits your week.</p>

<article class="card card-outdoor abs">
  <svg width="56" height="40" viewBox="0 0 56 40" fill="none" stroke="#fff" stroke-width="2.5"><path d="M4 36 L28 4 L52 36 Z"/><path d="M28 4 L22 36 M28 4 L34 36"/><path d="M2 36 H54"/></svg>
  <h3>Outdoor<br>Bootcamp Classes</h3>
  <p>Train in the fresh air with high energy circuits, partner drills and running work by the water.</p>
  <svg class="arrow" width="18" height="16" viewBox="0 0 18 16" fill="#fff"><path d="M0 6h11V1l7 7-7 7v-5H0z"/></svg>
</article>
<article class="card card-indoor abs">
  <svg width="56" height="40" viewBox="0 0 56 40" fill="none" stroke="#1b1b1b" stroke-width="2.5"><circle cx="14" cy="30" r="8"/><circle cx="42" cy="30" r="8"/><path d="M14 30 L26 12 L42 30 M26 12 H34 M22 8 H30"/></svg>
  <h3>Indoor<br>Training Classes</h3>
  <p>Functional strength classes with kettlebells, rigs and rowers, coached in a fully equipped studio.</p>
  <svg class="arrow" width="18" height="16" viewBox="0 0 18 16" fill="#1b1b1b"><path d="M0 6h11V1l7 7-7 7v-5H0z"/></svg>
</article>

<section class="gallery abs"></section>
<h2 class="section-title gallery-title abs">Photo Gallery</h2>
<div class="gallery-photo abs" style="left:140px;background:linear-gradient(160deg,#8aa0ad,#3c4a52)" role="img" aria-label="Athlete working on a gym rig"></div>
<div class="gallery-photo abs" style="left:372px;background:linear-gradient(160deg,#e6d2b0,#b89a72)" role="img" aria-label="Woman stretching on the beach"></div>
<div class="gallery-photo abs" style="left:604px;background:linear-gradient(160deg,#9a9a9a,#3d3d3d)" role="img" aria-label="Group class with weights"></div>
<div class="gallery-photo abs" style="left:836px;background:linear-gradient(160deg,#d9dde0,#8c7a6c)" role="img" aria-label="Man doing floor exercises"></div>
<div class="dots gallery-dots abs"><span class="on" style="background:#fff"></span><span></span><span></span><span></span></div>

<h2 class="section-title videos-title abs">Our Videos</h2>
<div class="video-thumb abs" style="left:148px;background:linear-gradient(160deg,#7a6a8a,#3a2f3c)" role="img" aria-label="Video of an indoor group workout">
  <svg class="play" width="40" height="40" viewBox="0 0 40 40"><circle cx="20" cy="20" r="19" fill="rgba(0,0,0,.4)" stroke="#fff" stroke-width="2"/><path d="M16 12 L29 20 L16 28 Z" fill="#fff"/></svg>
</div>
<div class="video-thumb abs" style="left:456px;background:linear-gradient(160deg,#c88a4a,#4a2a1a)" role="img" aria-label="Video of a cycling class">
  <svg class="play" width="40" height="40" viewBox="0 0 40 40"><circle cx="20" cy="20" r="19" fill="rgba(0,0,0,.4)" stroke="#fff" stroke-width="2"/><path d="M16 12 L29 20 L16 28 Z" fill="#fff"/></svg>
</div>
<div class="video-thumb abs" style="left:764px;background:linear-gradient(160deg,#9aa2aa,#4a4f55)" role="img" aria-label="Video of a step aerobics session">
  <svg class="play" width="40" height="40" viewBox="0 0 40 40"><circle cx="20" cy="20" r="19" fill="rgba(0,0,0,.4)" stroke="#fff" stroke-width="2"/><path d="M16 12 L29 20 L16 28 Z" fill="#fff"/></svg>
</div>

<section class="join abs" role="img" aria-label="Members training with kettlebells on the gym floor"></section>
<h2 class="section-title join-title abs">Join our gym now</h2>
<p class="join-text abs">Start with a free week of classes and get a training plan built around your goals and schedule.</p>
<div class="btn btn-outline abs">Click here</div>

<footer class="footer abs"></footer>
<nav class="footer-nav abs">
  <a href="#">HOME</a><a href="#">THE GYM</a><a href="#">THE BOOTCAMP</a><a href="#">PHOTO GALLERY</a><a href="#">ABOUT US</a><a href="#">CONTACT US</a>
</nav>
<p class="copyright abs">© 2017 Company Name . All rights reserved</p>
<div class="social abs"><span></span><span></span><span></span><span></span><span></span><span></span></div>

</body>
</html>
```